Velmora Freightway Solutions Business cards

Would like a very unique design catchy but professional for business cards. Please use log provided.Marlon WellsCeo and Founder TransCon Logistix Solutions1-888-913-3225mwells@tlsolutionsus.comwww.tlsolutionsus.com

```html
<!DOCTYPE html>
<html lang="en">
<head>
<meta charset="utf-8">
<title>Velmora Freightway Solutions — Business Cards</title>
<link rel="stylesheet" href="https://fonts.googleapis.com/css2?family=Cinzel:wght@600&family=Open+Sans:wght@400;600&display=swap">
<style>
  :root {
    --stage: #1d1e21;
    --brand-blue: #1272c0;
    --brand-blue-light: #3f86cc;
    --brand-red: #e3262c;
    --paper: #ffffff;
    --ink-light: #ffffff;
  }
  * { box-sizing: border-box; margin: 0; padding: 0; }
  html, body { width: 1200px; height: 800px; overflow: hidden; }
  body {
    background: var(--stage);
    font-family: "Open Sans", Arial, sans-serif;
    position: relative;
  }
  .card {
    position: absolute;
    width: 520px;
    height: 297px;
    border-radius: 18px;
    overflow: hidden;
    background: var(--brand-blue);
    color: var(--ink-light);
  }
  .card--front { left: 50px; top: 140px; }
  .card--back { left: 630px; top: 363px; }

  /* front */
  .brand {
    display: flex;
    align-items: center;
    gap: 12px;
    font-family: "Cinzel", Georgia, serif;
    font-weight: 600;
    letter-spacing: 1px;
  }
  .brand__square { width: 16px; height: 16px; flex: none; }
  .card--front .brand {
    position: absolute;
    left: 0; right: 0; top: 128px;
    justify-content: center;
    font-size: 22px;
    color: var(--ink-light);
  }
  .card--front .brand__square { background: var(--ink-light); }

  /* back */
  .back__panel {
    position: absolute;
    left: 0; top: 0; bottom: 0;
    width: 176px;
    background: var(--paper);
    border-right: 3px solid var(--brand-red);
    display: flex;
    align-items: center;
    justify-content: center;
  }
  .back__panel .brand {
    flex-direction: column;
    gap: 10px;
    text-align: center;
    font-size: 17px;
    line-height: 1.25;
    color: var(--brand-blue);
    padding: 0 14px;
  }
  .back__panel .brand__square { background: var(--brand-blue); }
  .back__decor {
    position: absolute;
    right: 36px; top: 34px;
    width: 200px; height: 200px;
    background: var(--brand-blue-light);
    opacity: 0.55;
  }
  .back__content {
    position: absolute;
    left: 204px; top: 34px; right: 24px;
  }
  .person__name {
    font-family: "Cinzel", Georgia, serif;
    font-weight: 600;
    font-size: 21px;
    letter-spacing: 1px;
  }
  .person__title { font-size: 12.5px; margin-top: 1px; }
  .rule { height: 1px; background: var(--ink-light); margin: 12px 0; }
  .company__name {
    font-family: "Cinzel", Georgia, serif;
    font-weight: 600;
    font-size: 15.5px;
    letter-spacing: 0.5px;
  }
  .company__address { font-size: 12.5px; line-height: 1.4; margin-top: 3px; }
  .contact { list-style: none; font-size: 12px; }
  .contact li { display: flex; align-items: center; gap: 8px; margin-bottom: 5px; }
  .contact svg { width: 15px; height: 15px; flex: none; }
</style>
</head>
<body>

  <section class="card card--front" aria-label="Card front">
    <div class="brand">
      <span class="brand__square"></span>
      <span>Velmora Freightway Solutions</span>
    </div>
  </section>

  <section class="card card--back" aria-label="Card back">
    <div class="back__panel">
      <div class="brand">
        <span class="brand__square"></span>
        <span>Velmora Freightway Solutions</span>
      </div>
    </div>
    <div class="back__decor"></div>
    <div class="back__content">
      <p class="person__name">Dorian Pike</p>
      <p class="person__title">CEO and Founder</p>
      <div class="rule"></div>
      <p class="company__name">Velmora Freightway Solutions</p>
      <p class="company__address">742 Larkspur Bend Rd,<br>Marietta, GA 30067</p>
      <div class="rule"></div>
      <ul class="contact">
        <li>
          <svg viewBox="0 0 16 16" aria-hidden="true"><circle cx="8" cy="8" r="7" fill="none" stroke="#fff" stroke-width="1.2"/><path d="M5.5 4.5l1.5 0 .6 2-1 .7a5 5 0 0 0 2.2 2.2l.7-1 2 .6v1.5c-3.5.3-6.3-2.5-6-6z" fill="#fff"/></svg>
          <span>1-888-470-6158</span>
        </li>
        <li>
          <svg viewBox="0 0 16 16" aria-hidden="true"><circle cx="8" cy="8" r="7" fill="none" stroke="#fff" stroke-width="1.2"/><rect x="4.2" y="5.3" width="7.6" height="5.4" fill="#fff"/><path d="M4.2 5.3L8 8.3l3.8-3" fill="none" stroke="#1272c0" stroke-width="0.9"/></svg>
          <span>dpike@vfwayroutes.com</span>
        </li>
        <li>
          <svg viewBox="0 0 16 16" aria-hidden="true"><circle cx="8" cy="8" r="7" fill="none" stroke="#fff" stroke-width="1.2"/><circle cx="8" cy="8" r="4" fill="none" stroke="#fff"/><path d="M4 8h8M8 4c-1.6 2.4-1.6 5.6 0 8M8 4c1.6 2.4 1.6 5.6 0 8" fill="none" stroke="#fff" stroke-width="0.8"/></svg>
          <span>www.vfwayroutes.com</span>
        </li>
      </ul>
    </div>
  </section>

</body>
</html>
```